Boutique custom software development company needs new business card

Our nearly 20 year old custom software development company would like to better include the fact that we are now providing Bitcoin services. These new services are B2B include education (how to acquire and securely hold Bitcoin) and integrating Bitcoin payments into existing ecommerce sites or other existing systems. Please keep the card clean and simple. Attached is our current design and some other files. vextorial.com

Target Market(s)

businesses owners interested in long term relationship

Industry/Entity Type

Custom software development and Bitcoin

Contact Information for Business Card

Dale Parker, dale@vextorial.com, vextorial.com, (888) 555-VXTRL

Font styles to use
Other font styles liked:
• monospace

Requirements
Must have
• double-sided
Nice to have
• clean and simple
Should not have
• physical address

```html
<!DOCTYPE html>
<html lang="en">
<head>
<meta charset="utf-8">
<title>Vextorial business card</title>
<link rel="stylesheet" href="https://fonts.googleapis.com/css2?family=Courier+Prime:wght@400;700&family=Lato:wght@400&display=swap">
<style>
  :root {
    --orange: #f07a22;
    --blue: #3c74ba;
    --navy: #1d2142;
    --paper: #fbfbfb;
    --white: #ffffff;
  }
  * { margin: 0; padding: 0; box-sizing: border-box; }
  html, body { width: 1200px; height: 1200px; overflow: hidden; }
  body {
    position: relative;
    background: linear-gradient(90deg, var(--white) 0 600px, var(--navy) 600px 1200px);
    font-family: "Courier Prime", "Courier New", monospace;
  }
  .card {
    position: absolute;
    width: 510px;
    height: 292px;
    box-shadow: 4px 6px 10px rgba(0, 0, 0, 0.28);
  }
  .card-front {
    left: 110px;
    top: 300px;
    z-index: 2;
    background: var(--orange);
    color: var(--white);
    display: flex;
    flex-direction: column;
    align-items: center;
    justify-content: center;
  }
  .front-name {
    font-weight: 700;
    font-size: 58px;
    letter-spacing: 1px;
    line-height: 1;
  }
  .front-tagline {
    margin-top: 14px;
    font-size: 14px;
    letter-spacing: 1.4px;
    white-space: nowrap;
  }
  .card-back {
    left: 585px;
    top: 445px;
    z-index: 1;
    display: flex;
  }
  .back-brand {
    position: relative;
    width: 255px;
    height: 100%;
    background: var(--paper);
    display: flex;
    align-items: center;
    justify-content: center;
    gap: 10px;
  }
  .brand-square {
    width: 22px;
    height: 22px;
    background: var(--orange);
  }
  .brand-name {
    color: var(--blue);
    font-weight: 700;
    font-size: 26px;
    letter-spacing: 0.5px;
  }
  .back-contact {
    position: relative;
    flex: 1;
    background: var(--blue);
    color: var(--white);
    padding: 112px 0 0 47px;
    font-size: 13.5px;
    line-height: 19px;
    letter-spacing: 1.4px;
  }
  .notch {
    position: absolute;
    left: -6px;
    top: 108px;
    width: 12px;
    height: 12px;
    border-radius: 50%;
    background: var(--paper);
  }
  .contact-list { list-style: none; }
  .brand-lockup {
    position: absolute;
    left: 110px;
    top: 770px;
    width: 510px;
    text-align: center;
  }
  .lockup-name {
    color: var(--blue);
    font-weight: 700;
    font-size: 48px;
    line-height: 1;
    letter-spacing: 1px;
  }
  .lockup-tagline {
    margin-top: 6px;
    color: var(--blue);
    font-family: "Lato", Arial, sans-serif;
    font-size: 16px;
    letter-spacing: -0.6px;
  }
</style>
</head>
<body>
  <section class="card card-front" aria-label="Card front">
    <div class="front-name">VEXTORIAL</div>
    <div class="front-tagline">custom software &amp; bitcoin services</div>
  </section>

  <section class="card card-back" aria-label="Card back">
    <div class="back-brand">
      <span class="brand-square"></span>
      <span class="brand-name">VEXTORIAL</span>
    </div>
    <div class="back-contact">
      <span class="notch"></span>
      <ul class="contact-list">
        <li>Dale Parker</li>
        <li>dale@vextorial.com</li>
        <li>vextorial.com</li>
        <li>(888) 555-VXTRL</li>
      </ul>
    </div>
  </section>

  <div class="brand-lockup">
    <div class="lockup-name">VEXTORIAL</div>
    <div class="lockup-tagline">developer of custom applications</div>
  </div>
</body>
</html>
```